Business Cards for IT Consulting Company (Managed Service Provider)

I am looking to have some business cards printed and would like some designs. We are an IT Consulting company based in Vancouver BC. I would like a nice clean and modern look to the cards. I have uploaded all the versions of my logo so parts can be used as needed. Here is a snippit from our website homepage:

Quillbrook Networks Ltd. is an IT Solutions Partner located in Vancouver BC, Canada. We offer IT solutions and support to customers in the greater Vancouver Area. With expertise in Microsoft platforms, as well as Linux and Mac OSX and over 12 years experience in the IT industry, Quillbrook Networks is dedicated to offering our clients top quality service and products. We take pride in the solutions we offer our customers. The greatest compliment a client can give us is to recommend our services.

Quillbrook Networks Ltd. offers a wide range of IT services from onsite service to remote support and managed service solutions. This allows clients to choose the support path that best suits their company’s needs. Supporting many different sized companies from small to enterprise level over the past 12 years Quillbrook Networks has the experience and expertise needed to ensure things run smoothly. Allowing our clients to focus on doing business.

Revolutionizing the way IT services are delivered.

Quillbrook Networks is dedicated to providing our clients with IT solutions that work and grow with them for years to come. This philosophy helps save money in the long run instead of replacing equipment constantly. Far too often IT solutions are not well thought out and while possibly solving the problem at hand, require replacement due to growth or quality within a very short time frame. Quillbrook Networks takes pride in providing solutions that will last and be able to accommodate growth without the need for replacement.

Industry/Entity Type

Information Technology

Contact Information for Business Card

Quillbrook Networks Ltd.
(Employee Name)
Eml: (Employees Email Address)
Web: quillbrook.me
Ph: 604-555-0148

Font styles to use
Serif
Sans Serif

Requirements
Must have
• The Company logo and company colors.
Nice to have
• - Our tag line: "Revolutionizing IT Services" or "Revolutionizing the way IT services are delivered."
• - Also I really like the idea of nature and technology together blending which is sort of where my logo came from so integrating that somehow onto the business cards would be great.

```html
<!DOCTYPE html>
<html lang="en">
<head>
<meta charset="utf-8">
<title>Quillbrook Networks Ltd. — Business Card</title>
<link rel="stylesheet" href="https://fonts.googleapis.com/css2?family=Source+Sans+3:wght@400;600&display=swap">
<style>
  :root {
    --brand-blue: #1ba6df;
    --brand-grey: #5f6062;
    --text-dark: #4a4b4d;
    --rule: #8a8b8d;
    --card-white: #ffffff;
    --backdrop: #3b3b3d;
    --pattern-blue: #2aa8e0;
  }
  * { box-sizing: border-box; margin: 0; padding: 0; }
  html, body {
    width: 1105px; height: 1200px; overflow: hidden;
    background: var(--backdrop);
    font-family: "Source Sans 3", sans-serif;
  }
  .canvas { position: relative; width: 1105px; height: 1200px; }

  .card { position: absolute; left: 196px; width: 720px; height: 413px; overflow: hidden; }

  /* Front */
  .card-front { top: 145px; background: var(--card-white); }
  .edge-stripe { position: absolute; left: 0; width: 14px; }
  .edge-stripe--grey { top: 0; height: 104px; background: var(--brand-grey); }
  .edge-stripe--blue { top: 118px; bottom: 0; background: var(--brand-blue); }

  .company-mark {
    position: absolute; top: 64px; right: 38px;
    display: flex; align-items: center; gap: 16px;
    color: var(--brand-blue); font-weight: 600;
  }
  .company-mark__dot { width: 50px; height: 50px; border-radius: 50%; border: 4px solid var(--brand-blue); flex: none; }
  .company-mark__name { font-size: 46px; line-height: 1; letter-spacing: -0.3px; }

  .person-name {
    position: absolute; left: 44px; top: 252px;
    font-size: 30px; font-weight: 600; color: var(--brand-blue);
  }
  .divider { position: absolute; left: 44px; right: 30px; top: 295px; height: 1.5px; background: var(--rule); }

  .contact-list { position: absolute; left: 44px; top: 307px; list-style: none; }
  .contact-list li {
    display: flex; align-items: center; gap: 10px;
    height: 27.5px; font-size: 19px; color: var(--text-dark);
  }
  .contact-list svg { width: 17px; height: 17px; fill: var(--brand-blue); flex: none; }

  .address {
    position: absolute; right: 30px; top: 335px; text-align: right;
    font-style: normal; font-size: 19px; line-height: 27.5px; color: var(--text-dark);
  }

  /* Back */
  .card-back { top: 602px; background: var(--brand-blue); }
  .back-pattern { position: absolute; inset: 0; background: linear-gradient(135deg, var(--pattern-blue), var(--brand-blue)); }
  .back-mark {
    position: absolute; left: 0; right: 0; top: 170px; text-align: center;
    color: var(--card-white); font-size: 40px; font-weight: 600;
  }
  .tagline {
    position: absolute; left: 0; right: 0; top: 325px; text-align: center;
    color: var(--card-white); font-size: 20px; font-weight: 600;
  }
</style>
</head>
<body>
<main class="canvas">

  <section class="card card-front" aria-label="Business card front">
    <div class="edge-stripe edge-stripe--grey"></div>
    <div class="edge-stripe edge-stripe--blue"></div>

    <div class="company-mark">
      <span class="company-mark__dot"></span>
      <span class="company-mark__name">Quillbrook Networks</span>
    </div>

    <h1 class="person-name">Dana Whitfield</h1>
    <div class="divider"></div>

    <ul class="contact-list">
      <li>
        <svg viewBox="0 0 24 24" aria-hidden="true"><path d="M6.6 10.8a15.2 15.2 0 0 0 6.6 6.6l2.2-2.2c.3-.3.7-.4 1-.2 1.1.4 2.3.6 3.6.6.6 0 1 .4 1 1V20c0 .6-.4 1-1 1A17 17 0 0 1 3 4c0-.6.4-1 1-1h3.5c.6 0 1 .4 1 1 0 1.3.2 2.5.6 3.6.1.3 0 .7-.2 1z"/></svg>
        604-555-0148
      </li>
      <li>
        <svg viewBox="0 0 24 24" aria-hidden="true"><path d="M2 5h20v2l-10 7L2 7z"/><path d="M2 9l10 7 10-7v10H2z"/></svg>
        dwhitfield@quillbrook.me
      </li>
      <li>
        <svg viewBox="0 0 24 24" aria-hidden="true"><circle cx="12" cy="12" r="10"/><path d="M8 6c2 1 1 3 3 4s0 3 2 4-1 4 1 5" fill="none" stroke="#fff" stroke-width="2"/></svg>
        www.quillbrook.me
      </li>
    </ul>

    <address class="address">
      2140 Larkspur Road<br>
      Anchorage, Alaska 34581
    </address>
  </section>

  <section class="card card-back" aria-label="Business card back">
    <div class="back-pattern" role="img" aria-label="Repeating light hexagon pattern on brand blue"></div>
    <p class="back-mark">Quillbrook</p>
    <p class="tagline">Revolutionizing IT Services</p>
  </section>

</main>
</body>
</html>
```